Tandem Hearth Works Pty Ltd

We need business cards for a company based in Perth, we install, service and maintain fire equipment.
On the front we want a great design with our logo and a small spot for our full company name, general company email address and office number. On the back we need space for our name, title, mobile number and email address on the back.

Target Market(s)

Facility managers and commercial/industrial building owners/occupiers.

Contact Information for Business Card

Font styles to use
Sans Serif

Requirements
Must have
• Please only submit 5 of your best samples.
Darker tones are preferred.
Nice to have
• We want to use, black, red and grey. Keep it modern and clean.
I've attached the company logo and a sample of a boarder we use on our emergency plans.
Should not have
• No preference. Let the designer choose.

```html
<!DOCTYPE html>
<html lang="en">
<head>
<meta charset="utf-8">
<title>Tandem Hearth Works Pty Ltd – Business Cards</title>
<link href="https://fonts.googleapis.com/css2?family=Arimo:wght@400;700&display=swap" rel="stylesheet">
<style>
  :root {
    --bg: #9a9a9a;
    --card: #ffffff;
    --red: #ed1c24;
    --band-red: #ff0000;
    --band-grey: #7a7a7a;
    --ink: #2b2b2b;
    --rule: #8a8a8a;
  }
  * { box-sizing: border-box; margin: 0; padding: 0; }
  html, body { width: 1200px; height: 1200px; overflow: hidden; }
  body {
    background: var(--bg);
    font-family: "Arimo", Arial, sans-serif;
    position: relative;
  }
  .card {
    position: absolute;
    top: 303px;
    width: 368px;
    height: 594px;
    background: var(--card);
    overflow: hidden;
  }
  .card--front { left: 200px; }
  .card--back { left: 600px; }
  .band { position: absolute; left: 0; width: 368px; height: 28px; display: block; }
  .band--top { top: 0; }
  .band--bottom { bottom: 0; transform: scale(-1, -1); }
  .wordmark {
    color: var(--red);
    font-weight: 700;
    letter-spacing: -2px;
    text-align: center;
    line-height: 1;
    position: absolute;
    left: 0; right: 0;
  }
  .card--front .wordmark { top: 235px; font-size: 118px; }
  .card--back .wordmark { top: 112px; font-size: 94px; }
  .details {
    position: absolute;
    top: 268px; left: 0; right: 0;
    text-align: center;
    color: var(--ink);
  }
  .person-name { color: var(--red); font-weight: 700; font-size: 25px; line-height: 28px; }
  .person-title { font-size: 19px; line-height: 24px; }
  .rule { width: 132px; height: 1px; background: var(--rule); margin: 13px auto; }
  .contact-line { font-size: 19px; line-height: 24px; }
  .company-name { color: var(--red); font-weight: 700; font-size: 22px; line-height: 27px; margin-top: 2px; }
  .office-phone { font-weight: 700; font-size: 24px; line-height: 30px; margin-top: 6px; }
  .office-web { font-size: 16.5px; line-height: 22px; margin-top: 10px; }
</style>
</head>
<body>
  <section class="card card--front">
    <svg class="band band--top" viewBox="0 0 368 28" aria-hidden="true">
      <polygon fill="var(--band-grey)" points="0,0 368,0 368,26 350,22 265,27 210,18 75,27 0,18"/>
      <polygon fill="var(--band-red)" points="30,16 205,0 212,4 75,27"/>
      <polygon fill="var(--band-red)" points="220,16 368,0 368,6 265,27"/>
    </svg>
    <div class="wordmark">THW</div>
    <svg class="band band--bottom" viewBox="0 0 368 28" aria-hidden="true">
      <polygon fill="var(--band-red)" points="0,0 368,0 368,26 350,22 265,27 210,18 75,27 0,18"/>
      <polygon fill="var(--band-grey)" points="30,16 205,0 212,4 75,27"/>
      <polygon fill="var(--band-grey)" points="220,16 368,0 368,6 265,27"/>
    </svg>
  </section>

  <section class="card card--back">
    <svg class="band band--top" viewBox="0 0 368 28" aria-hidden="true">
      <polygon fill="var(--band-grey)" points="0,0 368,0 368,26 350,22 265,27 210,18 75,27 0,18"/>
      <polygon fill="var(--band-red)" points="30,16 205,0 212,4 75,27"/>
      <polygon fill="var(--band-red)" points="220,16 368,0 368,6 265,27"/>
    </svg>
    <div class="wordmark">THW</div>
    <div class="details">
      <p class="person-name">MARCUS HALE</p>
      <p class="person-title">Managing Director</p>
      <div class="rule"></div>
      <p class="contact-line">555.0142.0142</p>
      <p class="contact-line">name@tandemhearth.com</p>
      <div class="rule"></div>
      <p class="company-name">TANDEM HEARTH<br>WORKS PTY LTD</p>
      <p class="office-phone">555.0190.0190</p>
      <p class="office-web">info@tandemhearth.com | www.tandemhearth.com</p>
    </div>
    <svg class="band band--bottom" viewBox="0 0 368 28" aria-hidden="true">
      <polygon fill="var(--band-red)" points="0,0 368,0 368,26 350,22 265,27 210,18 75,27 0,18"/>
      <polygon fill="var(--band-grey)" points="30,16 205,0 212,4 75,27"/>
      <polygon fill="var(--band-grey)" points="220,16 368,0 368,6 265,27"/>
    </svg>
  </section>
</body>
</html>
```